Business Card Design Project

Business card based on attached logo

Todd Merrick
Todd@lorvantest.com
877-514-9073 ext. 318
Www.LorvanTest.com

Industry/Entity Type

Business

```html
<!DOCTYPE html>
<html lang="en">
<head>
<meta charset="utf-8">
<title>LorvanTest Business Card Set</title>
<link rel="stylesheet" href="https://fonts.googleapis.com/css2?family=Arimo:wght@400;700&family=Source+Sans+3:wght@400&display=swap">
<style>
  :root {
    --stage: #ebe7e2;
    --label: #2a2522;
    --card: #ffffff;
    --card-grey: #f1f1f1;
    --ink: #111111;
    --ink-soft: #3a3a3a;
    --brand-red: #e31b23;
    --red-top: #c8232b;
    --red-bottom: #9e1a20;
    --divider: #9a9a9a;
    --panel-shadow: rgba(0, 0, 0, 0.22);
  }
  * { box-sizing: border-box; margin: 0; padding: 0; }
  html, body { width: 1200px; height: 788px; overflow: hidden; }
  body {
    position: relative;
    background: var(--stage);
    font-family: "Arimo", Arial, sans-serif;
  }
  .view-label {
    position: absolute;
    width: 526px;
    text-align: center;
    font-family: "Source Sans 3", Arial, sans-serif;
    font-size: 22px;
    color: var(--label);
  }
  .card {
    position: absolute;
    width: 526px;
    height: 300px;
    border-radius: 20px;
    overflow: hidden;
    background: var(--card);
  }
  .col-left { left: 53px; }
  .col-right { left: 622px; }
  .row-top { top: 74px; }
  .row-bottom { top: 445px; }

  .wordmark {
    display: flex;
    align-items: center;
    gap: 10px;
    font-weight: 700;
    color: var(--ink);
    letter-spacing: -1px;
    white-space: nowrap;
  }
  .wordmark-square {
    display: block;
    background: var(--brand-red);
  }

  /* Front */
  .front .wordmark {
    position: absolute;
    left: 22px;
    top: 100px;
    font-size: 36px;
  }
  .front .wordmark-square { width: 20px; height: 20px; }
  .front .divider {
    position: absolute;
    left: 266px;
    top: 84px;
    width: 2px;
    height: 116px;
    background: linear-gradient(to bottom, transparent, var(--divider) 30%, var(--divider) 70%, transparent);
  }
  .front .person-name {
    position: absolute;
    left: 292px;
    top: 111px;
    font-size: 18px;
    font-weight: 700;
    color: var(--brand-red);
  }
  .front .phone {
    position: absolute;
    left: 292px;
    top: 143px;
    display: flex;
    align-items: center;
    gap: 5px;
    font-size: 13px;
    color: var(--ink-soft);
  }
  .front .contact-band {
    position: absolute;
    left: 0;
    bottom: 0;
    width: 100%;
    height: 39px;
    background: var(--brand-red);
    display: flex;
    align-items: center;
    padding-left: 80px;
    gap: 26px;
    color: #ffffff;
    font-size: 15px;
  }
  .contact-item { display: flex; align-items: center; gap: 5px; }

  /* Backs */
  .back .wordmark {
    position: absolute;
    left: 0;
    width: 100%;
    justify-content: center;
    font-size: 50px;
  }
  .back .wordmark-square { width: 26px; height: 26px; }
  .back .wordmark { top: 96px; }
  .back .web {
    position: absolute;
    left: 0;
    width: 100%;
    bottom: 30px;
    text-align: center;
    font-family: "Source Sans 3", Arial, sans-serif;
    font-size: 19px;
    color: var(--ink-soft);
  }
  .back-red {
    background: linear-gradient(to bottom, var(--red-top), var(--red-bottom));
  }
  .back-red .web { color: #ffffff; }
  .back-grey { background: var(--card-grey); }
  .back-grey .logo-panel {
    position: absolute;
    left: 81px;
    top: 83px;
    width: 360px;
    height: 125px;
    background: #ffffff;
    box-shadow: 0 8px 10px -4px var(--panel-shadow), 0 0 0 1px #e2e2e2;
  }
  .back-grey .wordmark {
    top: 38px;
    font-size: 38px;
  }
  .back-grey .wordmark-square { width: 20px; height: 20px; }
</style>
</head>
<body>

  <div class="view-label col-left" style="top:33px;">Front</div>
  <div class="view-label col-right" style="top:33px;">Back - 1</div>
  <div class="view-label col-left" style="top:404px;">Back - 2</div>
  <div class="view-label col-right" style="top:404px;">Back - 3</div>

  <section class="card front col-left row-top">
    <div class="wordmark">LorvanTest<span class="wordmark-square"></span></div>
    <span class="divider"></span>
    <p class="person-name">Todd Merrick</p>
    <p class="phone">
      <svg width="11" height="11" viewBox="0 0 24 24" aria-hidden="true"><path fill="#e31b23" d="M6.6 10.8a15.1 15.1 0 0 0 6.6 6.6l2.2-2.2a1 1 0 0 1 1-.25 11.4 11.4 0 0 0 3.6.57 1 1 0 0 1 1 1V20a1 1 0 0 1-1 1A17 17 0 0 1 3 4a1 1 0 0 1 1-1h3.5a1 1 0 0 1 1 1c0 1.25.2 2.45.57 3.57a1 1 0 0 1-.25 1z"/></svg>
      877-514-9073 ext. 318
    </p>
    <div class="contact-band">
      <span class="contact-item">
        <svg width="13" height="10" viewBox="0 0 26 20" aria-hidden="true"><rect x="1" y="1" width="24" height="18" fill="none" stroke="#fff" stroke-width="2"/><path d="M1 1l12 10 12-10" fill="none" stroke="#fff" stroke-width="2"/></svg>
        Todd@lorvantest.com
      </span>
      <span class="contact-item">
        <svg width="9" height="9" viewBox="0 0 10 10" aria-hidden="true"><circle cx="5" cy="5" r="5" fill="#fff"/></svg>
        www.LorvanTest.com
      </span>
    </div>
  </section>

  <section class="card back col-right row-top">
    <div class="wordmark">LorvanTest<span class="wordmark-square"></span></div>
    <p class="web">www.LorvanTest.com</p>
  </section>

  <section class="card back back-red col-left row-bottom">
    <div class="wordmark">LorvanTest<span class="wordmark-square" style="background:#ffffff;"></span></div>
    <p class="web">www.LorvanTest.com</p>
  </section>

  <section class="card back back-grey col-right row-bottom">
    <div class="logo-panel">
      <div class="wordmark">LorvanTest<span class="wordmark-square"></span></div>
    </div>
    <p class="web">www.LorvanTest.com</p>
  </section>

</body>
</html>
```